We need a modern WIX website for Brightform Beam Services Australia (Laser/Industrial/Engineering)

We need a website for Wix (coded) for our laser restoration and industrial cleaning business.

It will need to be 4-6 pages.
Pages may include:
Home
About
Why Laser
Capabilities
There needs to be a contact / quote form

We do not want boring institutional design, so please do try to be a little creative (but not artsy, more engineering / laser etc). We hesitate with boxy wordpress looking templates, so please bring in strip backgrounds and sliders etc;

Our brand colours are blue and red, but a sharp modern site relative to the industry and work is important.

We envision the home page to take visitors on a informed journey of who, what, why, how, explaining the capability of laser science across contaminants, industries and surfaces.

We envision the home page to be strips:
- landing
- intro

-Why choose laser / What is laser cleaning
Minimum downtime, no surface damage, no environmental impact, no mess, no waste, complete restoration (we have an explainer video)

- Contaminants
Bacteria, Rust, Corrosion, Oxides, Grease, Oil, Paint, Stains, Mold, Soot / Carbon, Graffiti, Coatings, Dirt, Residue

- Surfaces
Metals, Engines/Parts/Components, Tools, Machinery, Bricks/Blockwork, Concrete, Paint, Stone, Wood, Aluminium

- Industries
Medical/Sterile, Hospitality, Bio Hazardous, Construction, Infrastructure, Property, Industrial, Engineer, Automotive, Marine, Heritage, Non Destructive Testing,

----
Here is some info on the company below:

"Background Information - Brightform Beam Services Australia (BBSA) is a leading provider of advanced laser restoration services for the residential, commercial, medical, hazardous and industrial sectors, offering waste free, chemical free and damage free complete restoration of metals, concrete, wood, stone and heritage, hygiene and hazard surfaces, with complete removal of coatings, bacteria, paint, rust, graffiti, mold and fire ash (soot), and preparation and treating for welding and bonding.
Servicing Melbourne and Victoria, with additional services available Australia wide, BBSA offers a 24/7 call-out service to your site.
With no downtime to your operations, we offer a timely resolution to your cleaning and maintenance needs."

We have attached some inspiration of websites we like the flow/feel of, but feel free to put your best designs forward.

You are welcome to use dummy headers and text at this stage, as design and feel is most important, and we can add text later.

```html
<!DOCTYPE html>
<html lang="en">
<head>
<meta charset="utf-8">
<title>Brightform Beam Services Australia</title>
<link href="https://fonts.googleapis.com/css2?family=Michroma&family=Roboto:wght@400;500;700&display=swap" rel="stylesheet">
<style>
:root{
  --red:#e31b23;
  --red-dark:#b3121a;
  --blue:#0d6bbd;
  --blue-bright:#1479d1;
  --black:#050505;
  --card:#151515;
  --white:#ffffff;
  --grey:#cfcfcf;
  --head:"Michroma",sans-serif;
  --body:"Roboto",sans-serif;
}
*{box-sizing:border-box;margin:0;padding:0}
html,body{width:1200px;height:4902px;overflow:hidden}
body{position:relative;background:var(--black);color:var(--white);font-family:var(--body)}
.abs{position:absolute}
.title{font-family:var(--head);font-weight:400;text-transform:uppercase;letter-spacing:1px;color:var(--white);line-height:1.2}
.title-bar{position:absolute;height:3px;width:44px;background:var(--white)}
.center{left:0;width:1200px;text-align:center}

/* header */
.brand{left:112px;top:34px;display:flex;align-items:center;gap:10px;font-family:var(--head);font-size:38px;color:var(--white);letter-spacing:2px;line-height:1}
.brand-mark{width:14px;height:14px;background:var(--white)}
.nav{top:52px;display:flex;font-size:12.5px;font-weight:700}
.nav a{position:absolute;color:var(--white);text-decoration:none;white-space:nowrap}
.nav a.active{color:var(--red)}
.nav-cta{left:786px;top:38px;width:131px;height:46px;background:var(--white);color:#111;font-size:12px;font-weight:700;display:flex;align-items:center;justify-content:center}
.social{width:28px;height:28px;border:1.5px solid var(--white);transform:rotate(45deg)}

/* hero */
.hero-photo{left:0;top:0;width:1200px;height:770px;clip-path:polygon(0 0,100% 0,100% 565px,50% 752px,0 565px);
  background:radial-gradient(ellipse 260px 120px at 560px 470px,rgba(255,170,60,.75),transparent 70%),
  radial-gradient(ellipse 500px 300px at 900px 200px,rgba(70,70,200,.7),transparent 70%),
  linear-gradient(160deg,#1d1f5e 0%,#2a2a8c 40%,#3b2f6d 70%,#201a40 100%)}
.hero-shade{left:0;top:0;width:1200px;height:770px;clip-path:polygon(0 0,100% 0,100% 565px,50% 752px,0 565px);background:rgba(5,5,30,.35)}
.hero-title{top:262px;font-size:31px;line-height:41px}
.hero-sub{top:365px;left:280px;width:640px;text-align:center;font-size:16px;line-height:28px}
.btn{background:var(--blue);color:var(--white);font-size:12.5px;font-weight:700;display:flex;align-items:center;justify-content:center;text-transform:uppercase}
.hero-btn{left:534px;top:449px;width:132px;height:42px}
.dot{top:678px;width:7px;height:7px;border-radius:50%;background:rgba(255,255,255,.5)}

/* industries */
.red-band{left:0;top:540px;width:1200px;height:841px;background:linear-gradient(180deg,#d2141c 0%,var(--red) 40%,#c9121a 100%)}
.slide-arrow{width:30px;height:30px;transform:rotate(45deg);border:1.5px solid var(--white)}
.slide-arrow.filled{background:var(--white)}
.industry-card{top:943px;width:305px;height:360px}
.industry-card span{position:absolute;left:0;right:0;bottom:24px;text-align:center;font-weight:700;font-size:17px}

/* about */
.about-frame{left:110px;top:1503px;width:300px;height:230px;border-top:6px solid var(--red);border-left:6px solid var(--red)}
.about-photo{left:137px;top:1529px;width:395px;height:392px;background:radial-gradient(circle at 190px 250px,rgba(255,190,110,.9),transparent 25%),linear-gradient(160deg,#2d63a8 0%,#123a6e 50%,#0a1830 100%)}
.about-bracket{left:530px;top:1625px;width:25px;height:296px;border:4px solid var(--white);border-left:none}
.badge{left:137px;top:1898px;width:141px;height:84px;background:var(--red);font-size:28px;font-weight:700;display:flex;align-items:center;justify-content:center}
.badge-note{left:310px;top:1942px;font-size:19px;font-weight:700}
.about-title{left:624px;top:1558px;font-size:35px}
.about-bar{left:624px;top:1614px;width:76px;background:var(--red)}
.about-text{left:624px;top:1648px;width:464px;font-size:13.5px;line-height:26.5px;text-align:justify}
.about-btn{left:624px;top:1872px;width:131px;height:45px}

/* why */
.why-photo{left:0;top:2100px;width:1200px;height:487px;background:linear-gradient(100deg,#1a2a44 0%,#2a3a55 35%,#3a3f4f 60%,#1b2233 100%)}
.why-photo::after{content:"";position:absolute;inset:0;background:radial-gradient(ellipse 140px 70px at 600px 430px,rgba(255,160,80,.5),transparent 70%),rgba(0,0,0,.35)}
.why-title{top:2172px;font-size:30px}
.why-text{top:2260px;left:165px;width:870px;text-align:center;font-size:14px;line-height:27px}
.play{left:558px;top:2368px;width:84px;height:84px;border-radius:50%;border:3px solid var(--white);display:flex;align-items:center;justify-content:center}
.play i{width:56px;height:56px;border-radius:50%;background:var(--white);display:flex;align-items:center;justify-content:center}
.feature{top:2522px;height:187px;background:var(--card)}
.feature-icon{position:absolute;left:50%;top:38px;width:60px;height:60px;margin-left:-30px;background:var(--red);transform:rotate(45deg)}
.feature-icon svg{position:absolute;left:15px;top:15px;transform:rotate(-45deg)}
.feature span{position:absolute;left:0;right:0;top:144px;text-align:center;font-weight:700;font-size:15px}
.chev{width:22px;height:22px}

/* surfaces */
.surf-title{left:110px;top:2874px;font-size:36px}
.surf-bar{left:110px;top:2930px;width:76px;background:var(--red)}
.surf-sub{left:110px;top:2963px;color:var(--blue-bright);font-weight:700;font-size:25px}
.surf-text{left:110px;top:3017px;width:436px;font-size:14px;line-height:27px;text-align:justify}
.surf-block{left:827px;top:2832px;width:261px;height:418px;background:var(--red)}
.surf-photo{left:601px;top:2870px;width:451px;height:342px;background:radial-gradient(circle at 250px 260px,rgba(255,160,70,.85),transparent 30%),linear-gradient(135deg,#1e2c3b 0%,#2b3747 50%,#141a22 100%)}

/* contaminants */
.cont-photo{left:0;top:3372px;width:1200px;height:590px;background:linear-gradient(180deg,#1d3540 0%,#24424b 50%,#1a2a2e 100%)}
.cont-photo::after{content:"";position:absolute;inset:0;background:radial-gradient(ellipse 200px 80px at 560px 560px,rgba(255,120,60,.35),transparent 70%),rgba(0,0,0,.3)}
.cont-title{top:3428px;font-size:30px}
.cont-card{width:230px;height:334px;border:2px solid var(--white);background:rgba(0,0,0,.18)}
.cont-icon{position:absolute;left:50%;top:54px;width:64px;height:64px;margin-left:-32px;background:var(--white);transform:rotate(45deg)}
.cont-icon svg{position:absolute;left:16px;top:16px;transform:rotate(-45deg)}
.cont-card h3{position:absolute;left:0;right:0;top:170px;text-align:center;font-size:16px;font-weight:700}
.cont-card p{position:absolute;left:12px;right:12px;top:202px;text-align:center;font-size:12.5px;line-height:24px}

/* contact */
.contact-band{left:0;top:3962px;width:1200px;height:940px;background:linear-gradient(180deg,#c51119 0%,var(--red) 45%,#cf141c 100%)}
.contact-title{top:4026px;font-size:31px}
.field{background:var(--white);color:#777;font-size:13px;padding:16px 16px 0}
.contact-btn{left:519px;top:4289px;width:160px;height:46px}

/* footer */
.f-col-line{top:4565px;width:1px;height:266px;background:#333}
.f-head{font-weight:700;font-size:16px}
.f-link{font-size:13.5px}
.f-bullet{width:12px;height:12px;border-radius:50%;background:var(--red)}
.f-small{font-size:11.5px;line-height:18px}
.f-label{font-size:14px;font-weight:500}
.f-input{left:805px;top:4629px;width:176px;height:46px;background:var(--white);color:#777;font-size:13px;padding:16px}
.f-join{left:980px;top:4629px;width:106px;height:46px}
.f-rule{left:110px;top:4835px;width:980px;height:1px;background:#333}
.copy{top:4862px;font-size:11.5px}
</style>
</head>
<body>

<!-- hero -->
<div class="abs red-band"></div>
<div class="abs hero-photo" role="img" aria-label="Laser cutting head throwing bright sparks over a metal workpiece"></div>
<div class="abs hero-shade"></div>
<svg class="abs" style="left:0;top:600px" width="1200" height="200" viewBox="0 600 1200 200">
  <polygon points="150,612 600,752 1050,612 600,766" fill="#ffffff"/>
  <polygon points="240,640 600,766 960,640 600,788" fill="#0d6bbd"/>
</svg>

<header>
  <div class="abs brand"><span class="brand-mark"></span>BBSA</div>
  <nav class="abs nav">
    <a class="active" style="left:392px">HOME</a>
    <a style="left:462px">ABOUT</a>
    <a style="left:538px">WHY LASER</a>
    <a style="left:647px">CAPABILITIES</a>
  </nav>
  <div class="abs nav-cta">CONTACT US</div>
  <div class="abs social" style="left:960px;top:47px"></div>
  <div class="abs social" style="left:1007px;top:47px"></div>
  <div class="abs social" style="left:1053px;top:47px"></div>
</header>

<section>
  <h1 class="abs title center hero-title">Brightform Beam<br>Services Australia</h1>
  <p class="abs hero-sub">Servicing Melbourne and Victoria, with additional services available Australia wide, BBSA offers a 24/7 call-out service to your site.</p>
  <div class="abs btn hero-btn">Get Started</div>
  <span class="abs dot" style="left:570px"></span>
  <span class="abs dot" style="left:588px;background:#fff"></span>
  <span class="abs dot" style="left:606px"></span>
  <span class="abs dot" style="left:624px"></span>
</section>

<!-- industries -->
<section>
  <h2 class="abs title center" style="top:844px;font-size:30px">Industries We Serve</h2>
  <div class="title-bar" style="left:578px;top:892px"></div>
  <div class="abs slide-arrow" style="left:1008px;top:857px"></div>
  <svg class="abs" style="left:1016px;top:865px" width="14" height="14" viewBox="0 0 14 14"><path d="M9 2 4 7l5 5" stroke="#fff" stroke-width="2" fill="none"/></svg>
  <div class="abs slide-arrow filled" style="left:1052px;top:857px"></div>
  <svg class="abs" style="left:1060px;top:865px" width="14" height="14" viewBox="0 0 14 14"><path d="M5 2l5 5-5 5" stroke="#e31b23" stroke-width="2" fill="none"/></svg>

  <div class="abs industry-card" style="left:110px;background:linear-gradient(180deg,#c9d3dc 0%,#e6b46f 45%,#2a2418 100%)" role="img" aria-label="Construction workers on scaffolding at sunset"><span>CONSTRUCTION</span></div>
  <div class="abs industry-card" style="left:447px;background:radial-gradient(circle at 150px 230px,rgba(150,200,255,.9),transparent 30%),linear-gradient(180deg,#2b3f55 0%,#17293d 100%)" role="img" aria-label="Industrial robot arm welding with blue sparks"><span>INDUSTRIAL</span></div>
  <div class="abs industry-card" style="left:784px;background:linear-gradient(160deg,#2a3e52 0%,#3a6a80 50%,#1b2a38 100%)" role="img" aria-label="Engineer beside a car with a holographic wireframe overlay"><span>AUTOMOTIVE</span></div>
</section>

<!-- about -->
<section>
  <div class="abs about-frame"></div>
  <div class="abs about-photo" role="img" aria-label="Laser cutting machine working on a steel sheet"></div>
  <div class="abs about-bracket"></div>
  <div class="abs badge">24/7</div>
  <div class="abs badge-note">CALL-OUT SERVICE</div>
  <h2 class="abs title about-title">About Us</h2>
  <div class="title-bar about-bar"></div>
  <p class="abs about-text">Brightform Beam Services Australia (BBSA) is a leading provider of advanced laser restoration services for the residential, commercial, medical, hazardous and industrial sectors, offering waste free, chemical free and damage free complete restoration of metals, concrete, wood, stone and heritage, hygiene and hazard surfaces, with complete removal of coatings, bacteria, paint, rust, graffiti, mold and fire ash (soot), and preparation and treating for welding and bonding.</p>
  <div class="abs btn about-btn">Learn More</div>
</section>

<!-- why laser -->
<section>
  <div class="abs why-photo" role="img" aria-label="Laser cleaning nozzle passing over a metal plate"></div>
  <h2 class="abs title center why-title">Why Choose Laser Cleaning?</h2>
  <div class="title-bar" style="left:555px;top:2222px;width:90px"></div>
  <p class="abs why-text">Lorem ipsum dolor sit amet, consectetur adipiscing elit, sed do eiusmod tempor incididunt ut labore et dolore magna aliqua. Ut enim ad minim veniam, quis nostrud exercitation ullamco laboris nisi ut aliquip ex ea commodo consequat. Duis aute irure dolor in reprehenderit in voluptate velit esse</p>
  <div class="abs play"><i><svg width="20" height="22" viewBox="0 0 20 22"><path d="M3 1l16 10L3 21z" fill="#0d6bbd"/></svg></i></div>

  <svg class="abs chev" style="left:48px;top:2633px" viewBox="0 0 22 22"><path d="M14 3 6 11l8 8" stroke="#888" stroke-width="2.5" fill="none"/></svg>
  <svg class="abs chev" style="left:1130px;top:2633px" viewBox="0 0 22 22"><path d="M8 3l8 8-8 8" stroke="#fff" stroke-width="2.5" fill="none"/></svg>

  <div class="abs feature" style="left:110px;width:229px"><div class="feature-icon"><svg width="30" height="30" viewBox="0 0 30 30" fill="none" stroke="#fff" stroke-width="2"><circle cx="15" cy="17" r="10"/><path d="M15 11v6l4 3M12 4h6M15 4v3"/></svg></div><span>MINIMUM DOWNTIME</span></div>
  <div class="abs feature" style="left:361px;width:227px"><div class="feature-icon"><svg width="30" height="30" viewBox="0 0 30 30" fill="none" stroke="#fff" stroke-width="2"><path d="M15 4l10 5v12l-10 5-10-5V9z M5 9l10 5 10-5M15 14v12"/></svg></div><span>NO SURFACE DAMAGE</span></div>
  <div class="abs feature" style="left:611px;width:226px"><div class="feature-icon"><svg width="30" height="30" viewBox="0 0 30 30" fill="none" stroke="#fff" stroke-width="2"><circle cx="15" cy="15" r="4"/><path d="M15 3v4M15 23v4M3 15h4M23 15h4M6.5 6.5l3 3M20.5 20.5l3 3M6.5 23.5l3-3M20.5 9.5l3-3"/><circle cx="15" cy="15" r="8.5"/></svg></div><span>NO MESS</span></div>
  <div class="abs feature" style="left:862px;width:226px"><div class="feature-icon"><svg width="30" height="30" viewBox="0 0 30 30" fill="none" stroke="#fff" stroke-width="2"><circle cx="15" cy="15" r="11"/><path d="M11 9h8l-1 13h-6zM10 9h10M7 23 23 7"/></svg></div><span>NO WASTE</span></div>
</section>

<!-- surfaces -->
<section>
  <h2 class="abs title surf-title">Surfaces</h2>
  <div class="title-bar surf-bar"></div>
  <h3 class="abs surf-sub">MACHINERY</h3>
  <p class="abs surf-text">Lorem ipsum dolor sit amet, consectetur adipiscing elit, sed do eiusmod tempor incididunt ut labore et dolore magna aliqua. Ut enim ad minim veniam, quis nostrud exercitation ullamco laboris nisi ut aliquip ex ea commodo consequat.</p>
  <div class="abs slide-arrow filled" style="left:117px;top:3160px;width:26px;height:26px"></div>
  <svg class="abs" style="left:124px;top:3167px" width="12" height="12" viewBox="0 0 12 12"><path d="M8 2 4 6l4 4" stroke="#000" stroke-width="2" fill="none"/></svg>
  <div class="abs slide-arrow" style="left:164px;top:3160px;width:26px;height:26px"></div>
  <svg class="abs" style="left:171px;top:3167px" width="12" height="12" viewBox="0 0 12 12"><path d="M4 2l4 4-4 4" stroke="#fff" stroke-width="2" fill="none"/></svg>
  <div class="abs surf-block"></div>
  <div class="abs surf-photo" role="img" aria-label="Welder in protective mask grinding metal with a shower of sparks"></div>
</section>

<!-- contaminants -->
<section>
  <div class="abs cont-photo" role="img" aria-label="Dim workshop with industrial machinery"></div>
  <h2 class="abs title center cont-title">We Clean Contaminants Like</h2>
  <div class="title-bar" style="left:555px;top:3478px;width:90px"></div>
  <svg class="abs chev" style="left:48px;top:3700px" viewBox="0 0 22 22"><path d="M14 3 6 11l8 8" stroke="#888" stroke-width="2.5" fill="none"/></svg>
  <svg class="abs chev" style="left:1130px;top:3700px" viewBox="0 0 22 22"><path d="M8 3l8 8-8 8" stroke="#fff" stroke-width="2.5" fill="none"/></svg>

  <div class="abs cont-card" style="left:110px;top:3526px"><div class="cont-icon"><svg width="32" height="32" viewBox="0 0 32 32" fill="none" stroke="#e31b23" stroke-width="2"><circle cx="16" cy="16" r="11"/><circle cx="13" cy="13" r="2.5"/><circle cx="20" cy="19" r="2"/><path d="M8 24 24 8"/></svg></div><h3>BACTERIA</h3><p>Lorem ipsum dolor sit amet, cons ectetur adipiscing elit, sed do eiusmod tempor incididunt ut labore et dolorea.</p></div>
  <div class="abs cont-card" style="left:361px;top:3560px"><div class="cont-icon"><svg width="32" height="32" viewBox="0 0 32 32" fill="none" stroke="#e31b23" stroke-width="2"><path d="M16 4l10 6v12l-10 6-10-6V10z"/><circle cx="16" cy="16" r="5"/></svg></div><h3>RUST</h3><p>Lorem ipsum dolor sit amet, cons ectetur adipiscing elit, sed do eiusmod tempor incididunt ut labore et dolorea.</p></div>
  <div class="abs cont-card" style="left:609px;top:3526px"><div class="cont-icon"><svg width="32" height="32" viewBox="0 0 32 32" fill="none" stroke="#e31b23" stroke-width="2"><rect x="6" y="18" width="20" height="8"/><path d="M12 6h8v6h-8zM16 12v6M10 22h4"/></svg></div><h3>CORROSION</h3><p>Lorem ipsum dolor sit amet, cons ectetur adipiscing elit, sed do eiusmod tempor incididunt ut labore et dolorea.</p></div>
  <div class="abs cont-card" style="left:858px;top:3560px"><div class="cont-icon"><svg width="32" height="32" viewBox="0 0 32 32" fill="none" stroke="#e31b23" stroke-width="2"><circle cx="14" cy="18" r="6"/><circle cx="22" cy="11" r="4"/><path d="M11 18h6"/></svg></div><h3>OXIDES</h3><p>Lorem ipsum dolor sit amet, cons ectetur adipiscing elit, sed do eiusmod tempor incididunt ut labore et dolorea.</p></div>
</section>

<!-- contact -->
<section>
  <div class="abs contact-band"></div>
  <h2 class="abs title center contact-title">Contact Us</h2>
  <div class="title-bar" style="left:578px;top:4076px"></div>
  <div class="abs field" style="left:165px;top:4121px;width:282px;height:48px">Full Name</div>
  <div class="abs field" style="left:458px;top:4121px;width:282px;height:48px">Phone Number</div>
  <div class="abs field" style="left:751px;top:4121px;width:284px;height:48px">Email Address</div>
  <div class="abs field" style="left:165px;top:4180px;width:870px;height:94px">Message</div>
  <div class="abs btn contact-btn">Send Message</div>
</section>

<!-- footer -->
<svg class="abs" style="left:0;top:4390px" width="1200" height="512" viewBox="0 4390 1200 512">
  <polygon points="160,4540 600,4397 1040,4540 600,4412" fill="#0d6bbd"/>
  <polygon points="80,4576 600,4408 1120,4576 600,4422" fill="#ffffff"/>
  <polygon points="0,4600 600,4418 1200,4600 1200,4902 0,4902" fill="#050505"/>
</svg>

<footer>
  <div class="abs brand" style="left:120px;top:4672px;font-size:34px"><span class="brand-mark"></span>BBSA</div>
  <div class="abs f-col-line" style="left:325px"></div>
  <div class="abs f-col-line" style="left:538px"></div>
  <div class="abs f-col-line" style="left:778px"></div>

  <h4 class="abs f-head" style="left:363px;top:4583px">QUICK LINKS</h4>
  <span class="abs f-bullet" style="left:364px;top:4629px"></span><span class="abs f-link" style="left:400px;top:4626px">Home</span>
  <span class="abs f-bullet" style="left:364px;top:4667px"></span><span class="abs f-link" style="left:400px;top:4664px">About</span>
  <span class="abs f-bullet" style="left:364px;top:4706px"></span><span class="abs f-link" style="left:400px;top:4703px">Why Laser</span>
  <span class="abs f-bullet" style="left:364px;top:4744px"></span><span class="abs f-link" style="left:400px;top:4741px">Capabilities</span>
  <span class="abs f-bullet" style="left:364px;top:4782px"></span><span class="abs f-link" style="left:400px;top:4779px">Contact Us</span>

  <h4 class="abs f-head" style="left:574px;top:4583px">CONTACT INFO</h4>
  <svg class="abs" style="left:573px;top:4626px" width="12" height="14" viewBox="0 0 12 14"><path d="M6 13S1 7.5 1 5a5 5 0 0 1 10 0c0 2.5-5 8-5 8z" fill="#e31b23"/><circle cx="6" cy="5" r="1.8" fill="#050505"/></svg>
  <span class="abs f-label" style="left:611px;top:4624px">ADDRESS:</span>
  <span class="abs f-small" style="left:611px;top:4644px">465, Lorum Ipsum Dolore,<br>United States</span>
  <svg class="abs" style="left:573px;top:4704px" width="13" height="13" viewBox="0 0 13 13"><path d="M2 1h3l1 3-2 1a7 7 0 0 0 4 4l1-2 3 1v3c0 1-1 1-2 1A11 11 0 0 1 1 3c0-1 0-2 1-2z" fill="#e31b23"/></svg>
  <span class="abs f-label" style="left:611px;top:4703px">PHONE:</span>
  <span class="abs f-small" style="left:611px;top:4723px">+1 (888) 888 8888</span>
  <svg class="abs" style="left:573px;top:4767px" width="14" height="11" viewBox="0 0 14 11"><rect width="14" height="11" fill="#e31b23"/><path d="M1 1l6 5 6-5" stroke="#050505" stroke-width="1.5" fill="none"/></svg>
  <span class="abs f-label" style="left:611px;top:4764px">EMAIL:</span>
  <span class="abs f-small" style="left:611px;top:4784px">info@bbsa.com</span>

  <h4 class="abs f-head" style="left:805px;top:4583px">JOIN NEWSLETTER</h4>
  <div class="abs f-input">Email Address</div>
  <div class="abs btn f-join">Join Now</div>
  <div class="abs social" style="left:812px;top:4707px;width:24px;height:24px"></div>
  <div class="abs social" style="left:858px;top:4707px;width:24px;height:24px"></div>
  <div class="abs social" style="left:905px;top:4707px;width:24px;height:24px"></div>

  <div class="abs f-rule"></div>
  <p class="abs center copy">© 2023 BBSA &nbsp;|&nbsp; All Rights Reserved</p>
</footer>

</body>
</html>
```